Mobile Fitness snd Therapy Business Card Design

I need a business card designed for my mobile fitness and therapy business.

Please view the images that I have uploaded. I like the simplicity of the design that I have attached. I adapted it with my information

Target Market(s)

Those seeking personal training, injury rehabilitation or massage therapy.

Industry/Entity Type

Business

Contact Information for Business Card

Derek Fulham - MSc, CAT(C), RMT, CSCS, Pn2
e-mail: derek@vantrelo.com
website: www.vantrelo.com
instagram: @derek_fulham

Font styles to use
Sans Serif

Colors
3176b5
0355a3

Requirements
Must have
• "Contact us to receive a FREE assessment"
• Services offered:
• Personal Training
• Golf Fitness
• Injury Rehab
• Massage Therapy
• Yoga
Nice to have
• Consistent colours with brand
• - Dark Blue: #232837
• - Blue: #5096f0
• Consistent look/feel with the website: www.vantrelo.com

```html
<!DOCTYPE html>
<html lang="en">
<head>
<meta charset="UTF-8">
<title>Vantrelo Business Card</title>
<link rel="stylesheet" href="https://fonts.googleapis.com/css2?family=Roboto:wght@400;500;700;900&family=Roboto+Condensed:wght@500;700&display=swap">
<style>
  :root {
    --navy: #222838;
    --blue: #2f5fd8;
    --blue-bright: #5096f0;
    --ink: #1f2433;
    --grey: #4a4d55;
    --paper: #f7f7f7;
    --backdrop: #e6e4e0;
    --white: #ffffff;
  }
  * { box-sizing: border-box; margin: 0; padding: 0; }
  html, body { width: 1200px; height: 960px; overflow: hidden; }
  body {
    background: var(--backdrop);
    font-family: "Roboto", Arial, sans-serif;
    position: relative;
  }
  .card {
    position: absolute;
    width: 600px;
    height: 342px;
    border-radius: 20px;
    overflow: hidden;
    box-shadow: 0 4px 12px rgba(0,0,0,0.18);
  }
  .card-front { left: 314px; top: 113px; background: var(--paper); }
  .card-back  { left: 311px; top: 472px; background: var(--navy); }

  .front-base-line {
    position: absolute; left: 0; right: 0; top: 324px; height: 4px;
    background: var(--blue);
  }
  .front-base-band {
    position: absolute; left: 0; right: 0; top: 328px; bottom: 0;
    background: var(--navy);
  }

  .brand { position: absolute; text-align: center; }
  .brand-name {
    font-family: "Roboto", Arial, sans-serif;
    font-weight: 700;
    letter-spacing: 0.06em;
    line-height: 1;
    display: block;
  }
  .brand-tagline {
    font-weight: 700;
    letter-spacing: 0.12em;
    display: block;
  }
  .card-front .brand { left: 64px; width: 240px; top: 154px; }
  .card-front .brand-name { font-size: 34px; color: var(--ink); }
  .card-front .brand-tagline { font-size: 10.5px; color: var(--ink); margin-top: 5px; }

  .divider {
    position: absolute; left: 330px; top: 108px; width: 2px; height: 130px;
    background: linear-gradient(to bottom, transparent, #9a9ca3 30%, #9a9ca3 70%, transparent);
  }
  .person { position: absolute; left: 359px; top: 117px; }
  .person-name {
    font-family: "Roboto Condensed", Arial Narrow, sans-serif;
    font-weight: 700; font-size: 22px; color: var(--blue); line-height: 1;
  }
  .person-credentials {
    font-family: "Roboto Condensed", Arial Narrow, sans-serif;
    font-weight: 700; font-size: 10px; color: var(--blue); margin-top: 5px;
  }
  .contact-list { list-style: none; margin-top: 22px; }
  .contact-list li {
    display: flex; align-items: center; gap: 7px;
    font-size: 14.5px; color: var(--grey); height: 19px;
  }
  .contact-list svg { width: 14px; height: 14px; flex: none; }

  .card-back .brand { left: 0; right: 0; top: 128px; }
  .card-back .brand-name { font-size: 50px; color: var(--white); }
  .card-back .brand-tagline { font-size: 15.5px; color: var(--white); margin-top: 10px; }

  .offer {
    position: absolute; left: 58px; width: 484px; top: 258px; height: 33px;
    border-radius: 17px; background: var(--blue);
    font-family: "Roboto Condensed", Arial Narrow, sans-serif;
    font-weight: 700; font-size: 21px; color: var(--white);
    display: flex; align-items: center; justify-content: center;
  }
  .services {
    position: absolute; left: 0; right: 0; top: 297px;
    text-align: center; font-size: 14.5px; color: var(--white);
  }
  .services .sep { color: var(--blue-bright); margin: 0 3px; }
</style>
</head>
<body>
  <section class="card card-front">
    <div class="brand">
      <span class="brand-name">VANTRELO</span>
      <span class="brand-tagline">NUTRITION - FITNESS - HEALTH</span>
    </div>
    <div class="divider"></div>
    <div class="person">
      <h1 class="person-name">DEREK FULHAM</h1>
      <p class="person-credentials">MSC, CAT(C), RMT, CSCS, PN2</p>
      <ul class="contact-list">
        <li>
          <svg viewBox="0 0 14 14" aria-hidden="true"><rect x="1" y="3" width="12" height="8.5" rx="1" fill="#2f5fd8"/><path d="M1.5 3.6 7 7.8l5.5-4.2" stroke="#fff" stroke-width="1.2" fill="none"/></svg>
          derek@vantrelo.com
        </li>
        <li>
          <svg viewBox="0 0 14 14" aria-hidden="true"><circle cx="7" cy="7" r="6" fill="#2f5fd8"/><ellipse cx="7" cy="7" rx="2.6" ry="6" stroke="#fff" stroke-width="1" fill="none"/><path d="M1 7h12" stroke="#fff" stroke-width="1"/></svg>
          www.vantrelo.com
        </li>
        <li>
          <svg viewBox="0 0 14 14" aria-hidden="true"><circle cx="7" cy="7" r="6" fill="#2f5fd8"/></svg>
          @derek_fulham
        </li>
      </ul>
    </div>
    <div class="front-base-line"></div>
    <div class="front-base-band"></div>
  </section>

  <section class="card card-back">
    <div class="brand">
      <span class="brand-name">VANTRELO</span>
      <span class="brand-tagline">NUTRITION - FITNESS - HEALTH</span>
    </div>
    <p class="offer">CONTACT US TO RECEIVE A FREE ASSESSMENT</p>
    <p class="services">Personal Training<span class="sep">|</span>Golf Fitness<span class="sep">|</span>Injury Rehab<span class="sep">|</span>Massage Therapy<span class="sep">|</span>Yoga</p>
  </section>
</body>
</html>
```